Defense contractor needs a roll-up for an exhibition

The booth we have booked has only a size of 3m².
So this will be the centerpiece of the whole booth.
We need a roll-up that attracts visitors and at the same time it should contain already designed graphics. These graphics are giving visitors an overview of our system. So it is necessary to have them exposed in a height that the booth personal can conveniently point with its fingers at them.
For information about our company and product visit:
https://www.brellowtrackline.com/
For designing you should use Adobe Illustrator and the templates provided in the zip file, to guarantee a perfect print.
I have supplied my business card that you can copy the logo. As the company logo will be already at the booth nearby the top of the roll-up, you should not place it there. It can be in the middle or at the bottom.
I have uploaded a picture of the booth. The roll up will be placed at the left of the screen and has a size of 80cm x 200cm

Defense

Defense

Serif

0054AA
0677BA
7BADD7
CADEEF
E8F1F8

• you must use the Adobe Illustrator template to have a good printing result
• company logo on the upper side of the roll-up

```html
<!DOCTYPE html>
<html lang="en">
<head>
<meta charset="utf-8">
<title>Brellow Trackline – Roll-up</title>
<link rel="stylesheet" href="https://fonts.googleapis.com/css2?family=Montserrat:wght@300;400;500;600;700;800&display=swap">
<style>
  :root {
    --page: #efefef;
    --navy: #0a1550;
    --navy-deep: #07103e;
    --green: #6f9a6a;
    --silver: #c9ccd4;
    --white: #ffffff;
    --ink: #111111;
    --rule: #1d2a6a;
  }
  * { margin: 0; padding: 0; box-sizing: border-box; }
  html, body {
    width: 800px; height: 1200px; overflow: hidden;
    background: var(--page);
    font-family: "Montserrat", sans-serif;
  }
  .rollup {
    position: absolute; left: 165px; top: 20px;
    width: 471px; height: 1160px;
    background: var(--navy);
    overflow: hidden;
    box-shadow: 0 6px 24px rgba(0,0,0,.18);
  }
  .photo {
    position: absolute; left: 0; top: 560px; width: 471px; height: 510px;
    background:
      radial-gradient(ellipse 60% 35% at 40% 55%, rgba(226,128,38,.85), rgba(226,128,38,0) 75%),
      linear-gradient(180deg, var(--navy) 0%, #2a3266 24%, #7a4a28 48%, #5b4636 72%, #6a6e76 100%);
  }
  .header { position: absolute; left: 0; top: 0; width: 471px; height: 140px; }
  .header svg { position: absolute; left: 0; top: 0; }
  .brand-name {
    position: absolute; left: 0; top: 50px; width: 471px;
    text-align: center; color: var(--white);
    font-weight: 800; font-size: 27px; line-height: 32px; letter-spacing: .3px;
  }
  .headline { position: absolute; left: 0; top: 168px; width: 471px; text-align: center; }
  .headline-strong {
    color: var(--green); font-weight: 800; font-size: 36px; line-height: 42px;
  }
  .headline-for {
    color: var(--white); font-weight: 400; font-size: 34px; line-height: 46px;
    display: flex; align-items: center; justify-content: center; gap: 6px;
  }
  .headline-for .dash { display: inline-flex; flex-direction: column; gap: 4px; }
  .headline-for .dash i { display: block; height: 2px; background: var(--white); }
  .headline-light {
    color: var(--white); font-weight: 300; font-size: 31px; line-height: 39px;
  }
  .headline-light .em { font-size: 34px; font-weight: 400; }
  .services-bar { position: absolute; left: 0; top: 398px; width: 471px; height: 38px; }
  .services-label {
    position: absolute; left: 0; top: 404px; width: 471px; text-align: center;
    color: var(--white); font-weight: 500; font-size: 21px; line-height: 26px;
  }
  .intro {
    position: absolute; left: 10px; top: 447px; width: 451px; text-align: center;
    color: var(--white); font-size: 15px; line-height: 20px; font-weight: 400;
  }
  .service {
    position: absolute; display: flex; align-items: flex-start; gap: 16px;
    color: var(--white); font-weight: 600; font-size: 16px; line-height: 18.7px;
  }
  .service .badge { flex: none; width: 56px; height: 56px; }
  .footer {
    position: absolute; left: 0; top: 1064px; width: 471px; height: 96px; background: var(--white);
  }
  .phone-pill {
    position: absolute; left: 56px; top: 1050px; width: 359px; height: 44px;
    background: var(--ink); border-radius: 22px;
    display: flex; align-items: center; gap: 12px; padding-left: 6px;
    color: var(--white); font-weight: 700; font-size: 36px; line-height: 44px; letter-spacing: 1.5px;
  }
  .phone-pill .phone-icon { flex: none; width: 36px; height: 36px; }
  .web {
    position: absolute; left: 0; top: 1101px; width: 471px; text-align: center;
    color: var(--ink); font-weight: 600; font-size: 20px; line-height: 24px;
  }
</style>
</head>
<body>
<main class="rollup">
  <div class="photo" role="img" aria-label="Photograph of a soldier in combat gear standing before a tank amid fire and smoke"></div>

  <header class="header">
    <svg width="471" height="140" viewBox="0 0 471 140">
      <rect width="471" height="103" fill="var(--navy-deep)"/>
      <polyline points="0,104 56,104 107,136 374,136 425,104 471,104" fill="none" stroke="var(--silver)" stroke-width="3"/>
    </svg>
    <div class="brand-name">BRELLOW TRACKLINE</div>
  </header>

  <section class="headline">
    <div class="headline-strong">ADVANCED COMBAT<br>TRAINING SYSTEMS</div>
    <div class="headline-for">
      <span class="dash"><i style="width:30px"></i><i style="width:22px;margin-left:8px"></i></span>
      FOR
      <span class="dash"><i style="width:30px"></i><i style="width:22px"></i></span>
    </div>
    <div class="headline-light">REALISTIC COMBAT<br><span class="em">SIMULATION</span></div>
  </section>

  <svg class="services-bar" width="471" height="38" viewBox="0 0 471 38">
    <line x1="15" y1="16" x2="456" y2="16" stroke="var(--rule)" stroke-width="2"/>
    <path d="M100,0 H372 Q358,2 352,14 L342,32 Q338,38 328,38 H144 Q134,38 130,32 L120,14 Q114,2 100,0 Z" fill="var(--green)"/>
  </svg>
  <div class="services-label">OUR SERVICES</div>

  <p class="intro">The signature of the contract is not the end - it is just<br>the beginning of a long-lasting partnership.</p>

  <section class="service-list">
    <div class="service" style="left:55px;top:507px">
      <svg class="badge" viewBox="0 0 56 56"><circle cx="28" cy="28" r="27" fill="none" stroke="var(--white)" stroke-dasharray="2 2"/><circle cx="28" cy="28" r="23" fill="var(--green)"/><circle cx="28" cy="28" r="18" fill="var(--white)"/><path d="M28 17 L36 20 V28 Q36 35 28 39 Q20 35 20 28 V20 Z" fill="none" stroke="var(--navy)" stroke-width="1.6"/><path d="M24 28 L27 31 L32 25" fill="none" stroke="var(--navy)" stroke-width="1.6"/></svg>
      <span class="label">Extended<br>warranty<br>programs</span>
    </div>
    <div class="service" style="left:55px;top:573px">
      <svg class="badge" viewBox="0 0 56 56"><circle cx="28" cy="28" r="27" fill="none" stroke="var(--white)" stroke-dasharray="2 2"/><circle cx="28" cy="28" r="23" fill="var(--green)"/><circle cx="28" cy="28" r="18" fill="var(--white)"/><circle cx="28" cy="24" r="5" fill="none" stroke="var(--navy)" stroke-width="1.6"/><path d="M19 38 Q19 30 28 30 Q37 30 37 38 Z" fill="none" stroke="var(--navy)" stroke-width="1.6"/></svg>
      <span class="label">Logistics<br>support</span>
    </div>
    <div class="service" style="left:55px;top:640px">
      <svg class="badge" viewBox="0 0 56 56"><circle cx="28" cy="28" r="27" fill="none" stroke="var(--white)" stroke-dasharray="2 2"/><circle cx="28" cy="28" r="23" fill="var(--green)"/><circle cx="28" cy="28" r="18" fill="var(--white)"/><rect x="21" y="18" width="14" height="20" fill="none" stroke="var(--navy)" stroke-width="1.6"/><path d="M24 24 H32 M24 28 H32 M24 32 H29" stroke="var(--navy)" stroke-width="1.4"/></svg>
      <span class="label">Maintenance<br>contracts</span>
    </div>
    <div class="service" style="left:244px;top:507px">
      <svg class="badge" viewBox="0 0 56 56"><circle cx="28" cy="28" r="27" fill="none" stroke="var(--white)" stroke-dasharray="2 2"/><circle cx="28" cy="28" r="23" fill="var(--green)"/><circle cx="28" cy="28" r="18" fill="var(--white)"/><circle cx="23" cy="23" r="3.5" fill="none" stroke="var(--navy)" stroke-width="1.6"/><circle cx="33" cy="33" r="3.5" fill="none" stroke="var(--navy)" stroke-width="1.6"/><path d="M27 23 H36 M20 33 H29" stroke="var(--navy)" stroke-width="1.6"/></svg>
      <span class="label" style="margin-top:3px">long-term<br>spare<br>part<br>services to<br>keep the<br>equipment<br>in perfect<br>operational<br>condition</span>
    </div>
  </section>

  <div class="footer"></div>
  <div class="phone-pill">
    <svg class="phone-icon" viewBox="0 0 36 36"><circle cx="18" cy="18" r="17" fill="var(--white)"/><path d="M12 10 Q10 11 10 14 Q12 22 22 26 Q25 26 26 24 L23 20 L20 22 Q16 20 14 16 L16 13 Z" fill="var(--ink)"/></svg>
    <span>49 1632907518</span>
  </div>
  <div class="web">www.brellowtrackline.com</div>
</main>
</body>
</html>
```